PixelHarbor Rangers (Ledgerline Nova)
A website dedicated to crypto education. We are a new company focused on blockchain edutainment (education and interesting and entertaining content about the blockchain space). We want a fun, clean/minimalist and modern website that is made up of an education platform which could be a website in it’s own right. It will be the reference point for our users/community for all of our other blockchain based content in the PHR website ecosystem which will be covering; crypto news, digital asset investing (including a technical and fundamental analysis subscription service), blockchain business solutions and an NFT section that will cover creative art projects (art, music, gaming and more). To feature a logins and payment system which may need a shopping basket set up for tutorial/educational platform that is accessed via the website, NFT page with sub-categories: education and NFT and metaverse/virtual world and merchandise shopping page which is Web 3.0 enabled (able to link to a VeloPurse, Tallow Vault etc , digital asset education page featuring blog and newsletter subscriptions links, A social media page where people can access videos, podcasts and our presence on other platforms such as Chirplo, Snapmora, Huddlex, Wirepost etc.
Number of Pages Required
5+ page
Look and feel

```html
<!DOCTYPE html>
<html lang="en">
<head>
<meta charset="utf-8">
<title>Ledgerline Nova – Dark and Light Themes</title>
<link href="https://fonts.googleapis.com/css2?family=Poppins:wght@400;500;600;700&display=swap" rel="stylesheet">
<style>
:root{
  --page:#c9d3fa;
  --blue:#3f5cf4;
  --blue-soft:#d6ddfc;
  --ink:#1b1b1d;
  --foot-deep:#1c1c1e;
  --foot:#252527;
}
*{box-sizing:border-box;margin:0;padding:0}
html,body{width:1200px;height:2657px;overflow:hidden;background:var(--page);font-family:'Poppins',sans-serif}
.stage{position:relative;width:1163px;height:2576px;transform:scale(1.031814);transform-origin:0 0}
.panel{position:absolute;top:50px;width:540px;height:2476px;background:var(--bg);overflow:hidden;color:var(--text)}
.panel--dark{left:26px;
  --bg:#252527;--alt:#1c1c1e;--deep:#19191b;--text:#fff;--title:var(--blue);--sub:#fff;
  --card:#1d1d1f;--card-title:#fff;--tile:#1b1b1d;--tile-label:var(--blue);--more:#333;--feature:#1d1d1f;--feature-title:var(--blue)}
.panel--light{left:595px;
  --bg:#fff;--alt:var(--blue-soft);--deep:var(--blue-soft);--text:#222;--title:#1b1b1d;--sub:#1b1b1d;
  --card:var(--blue-soft);--card-title:var(--blue);--tile:#ebecf0;--tile-label:var(--blue);--more:#1b1b1d;--feature:#fff;--feature-title:#1b1b1d}
.abs{position:absolute}
.band{position:absolute;left:0;width:540px}
.band--alt{background:var(--alt)}
.band--deep{background:var(--deep)}

.hero-shape{position:absolute;left:0;top:0;width:305px;height:304px;background:var(--blue);border-bottom-right-radius:110px}
.brand{position:absolute;left:33px;top:17px;font-size:12px;font-weight:700;color:#fff}
.nav{position:absolute;left:166px;top:20px;display:flex;gap:12px;font-size:6.5px;font-weight:500;color:#fff}
.nav span:nth-child(n+4){color:var(--sub)}
.login{position:absolute;left:430px;top:15px;width:51px;height:20px;border-radius:10px;background:var(--blue);border:1.5px solid #fff;color:#fff;font-size:6.5px;font-weight:600;display:flex;align-items:center;justify-content:center}
.cart{position:absolute;left:489px;top:19px}
.hero-title{position:absolute;left:35px;top:86px;font-size:21.5px;line-height:25px;font-weight:700;color:#fff}
.hero-sub{position:absolute;left:34px;top:142px;font-size:12.5px;line-height:17px;font-weight:600;color:#fff}
.btn{position:absolute;height:24px;width:80px;border-radius:12px;background:var(--blue);color:#fff;font-size:7.5px;font-weight:600;display:flex;align-items:center;justify-content:center}
.btn--black{background:#111}
.dots{position:absolute;left:34px;top:253px;display:flex;gap:4px}
.dots i{display:block;width:13px;height:2px;background:#fff}
.media{position:absolute;border-radius:22px}
.tilt{transform:rotate(-4deg) skewX(-3deg)}
.tilt-r{transform:rotate(4deg) skewX(3deg)}

.sec-title{position:absolute;font-size:16.5px;line-height:18px;font-weight:700;color:var(--title)}
.copy{position:absolute;width:230px;font-size:6.4px;line-height:12px;color:var(--text)}
.copy p+p{margin-top:5px}
.center-title{position:absolute;left:0;width:540px;text-align:center;font-size:16px;font-weight:700;color:var(--sub)}

.tile{position:absolute;top:1095px;width:108px;height:97px;border-radius:16px;background:var(--tile);display:flex;flex-direction:column;align-items:center;justify-content:center;gap:6px;font-size:11px;font-weight:500;color:var(--tile-label)}
.tile--more{color:var(--more)}

.thumb{position:absolute;display:flex;align-items:center;justify-content:center}
.play{width:22px;height:22px;border-radius:50%;border:2px solid #fff;display:flex;align-items:center;justify-content:center}
.play::after{content:"";margin-left:2px;border-left:7px solid #fff;border-top:4.5px solid transparent;border-bottom:4.5px solid transparent}
.play--big{width:38px;height:38px;border-width:3px}
.play--big::after{border-left-width:12px;border-top-width:8px;border-bottom-width:8px}

.head-row{position:absolute;left:34px;width:472px;display:flex;justify-content:space-between;align-items:center}
.head-row h3{font-size:16.5px;font-weight:700;color:var(--sub)}
.head-row a{font-size:7px;font-weight:500;color:var(--sub);text-decoration:underline}
.card{position:absolute;width:151px;height:85px;border-radius:6px;background:var(--card);padding:9px 9px 0}
.card h4{font-size:8px;font-weight:600;color:var(--card-title);margin-bottom:3px}
.card p{font-size:6px;line-height:12px;color:var(--text)}
.card .date{font-size:5.5px;color:var(--text);opacity:.7;margin-bottom:2px;line-height:8px}
.card-foot{position:absolute;left:9px;right:9px;bottom:7px;display:flex;justify-content:space-between;font-size:5px;color:var(--blue);font-weight:500}
.card-foot span+span{margin-left:5px}
.feature-art{position:absolute;left:34px;width:147px;height:181px;border-radius:16px}

.feature{position:absolute;left:289px;top:1780px;width:217px;height:140px;border-radius:16px;background:var(--feature);padding:12px 12px;box-shadow:0 2px 8px rgba(0,0,0,.12)}
.feature h3{font-size:16px;font-weight:700;color:var(--feature-title);margin-bottom:5px}
.feature p{font-size:6px;line-height:12px;color:var(--text)}

.web3{position:absolute;left:0;top:2220px;width:540px;height:65px;background:var(--foot-deep);color:#fff;font-size:7.5px;font-weight:600}
.web3 .row{position:absolute;top:26px;display:flex;align-items:center;gap:8px}
.dot{display:inline-block;width:12px;height:12px;border-radius:50%;background:#e2761b}
.sq{display:inline-block;width:11px;height:12px;border:1.5px solid var(--blue);border-radius:2px}
.vault{color:var(--blue);font-weight:500;font-size:9px}
.social{color:var(--blue);font-weight:500;font-size:6.5px}
.footer{position:absolute;left:0;top:2285px;width:540px;height:153px;background:var(--foot);color:#fff}
.footer h5{font-size:8.5px;font-weight:600;color:var(--blue);margin-bottom:4px}
.footer .f-brand{font-size:12px;color:#fff;font-weight:700;margin-bottom:6px}
.footer li{list-style:none;font-size:6px;line-height:13px}
.footer p{font-size:6px;line-height:13px}
.col{position:absolute;top:22px}
.email{width:108px;height:20px;border-radius:10px;background:#fff;color:#555;font-size:5.5px;display:flex;align-items:center;padding-left:9px;margin-top:8px}
.signup{width:108px;height:20px;border-radius:10px;background:var(--blue);color:#fff;font-size:7px;font-weight:600;display:flex;align-items:center;justify-content:center;margin-top:6px}
.copyright{position:absolute;left:0;top:2438px;width:540px;height:38px;background:var(--foot);border-top:1px solid #333;color:#fff;font-size:5.5px}
.pays{position:absolute;right:16px;top:13px;display:flex;gap:3px}
.pays i{display:block;width:15px;height:9px;border-radius:2px;background:#d9d9dd}
</style>
</head>
<body>
<div class="stage">

<!-- ============ DARK THEME ============ -->
<section class="panel panel--dark">
  <div class="hero-shape"></div>
  <div class="brand">Ledgerline Nova</div>
  <nav class="nav"><span>Home</span><span>About Us</span><span>Services</span><span>Projects</span><span>Podcast</span><span>Latest News</span></nav>
  <div class="login">Log In</div>
  <svg class="cart" width="14" height="10" viewBox="0 0 14 10"><path d="M1 3h10l-1.5 5h-7z" fill="#fff"/><text x="10" y="3" font-size="4" fill="#3f5cf4" font-family="Poppins,sans-serif">(0)</text></svg>
  <h1 class="hero-title">Welcome to<br>Ledgerline Nova</h1>
  <p class="hero-sub">We are a website dedicated<br>to crypto education</p>
  <div class="btn btn--black" style="left:35px;top:189px">Read More</div>
  <div class="dots"><i></i><i></i><i></i><i></i></div>
  <div class="media" role="img" aria-label="Neon NFT artwork with pixel cat character and floating media icons" style="left:236px;top:50px;width:270px;height:205px;background:radial-gradient(circle at 50% 60%,#1e6fa0,#0d1c33 60%,#070b16)"></div>

  <h2 class="sec-title" style="left:34px;top:346px">Digital Asset Investing</h2>
  <div class="copy" style="left:34px;top:373px"><p>Sed ut perspiciatis unde omnis iste natus error sit voluptatem accus antium beatae enim ipsam voluptatem quia voluptas sit aspernatur aut odit aut fugit, sed quia consequuntur magni dolores eos qui ratione voluptatem sequi nesciunt.</p><p>Sed ut perspiciatis unde omnis iste natus error sit voluptatem accus antium beatae enim ipsam voluptatem quia voluptas sit aspernatur aut odit aut fugit, sed quia consequuntur magni dolores eos qui ratione voluptatem sequi nesciunt.</p></div>
  <div class="btn" style="left:35px;top:487px">Read More</div>
  <div class="media tilt" role="img" aria-label="Hand holding phone with glowing crypto interface" style="left:284px;top:344px;width:218px;height:182px;background:linear-gradient(135deg,#6aa6b4,#1c3c4a 55%,#0e1a22)"></div>

  <h2 class="sec-title" style="left:276px;top:569px">Blockchain Business<br>Solutions</h2>
  <div class="copy" style="left:277px;top:611px"><p>Sed ut perspiciatis unde omnis iste natus error sit voluptatem accus antium beatae enim ipsam voluptatem quia voluptas sit aspernatur aut odit aut fugit, sed quia consequuntur magni dolores eos qui ratione voluptatem sequi nesciunt.</p><p>Sed ut perspiciatis unde omnis iste natus error sit voluptatem accus antium beatae enim ipsam voluptatem quia voluptas sit aspernatur aut odit aut fugit, sed.</p></div>
  <div class="btn" style="left:277px;top:709px">Read More</div>
  <div class="media tilt-r" role="img" aria-label="Open hand holding a glowing network sphere" style="left:38px;top:566px;width:222px;height:186px;background:radial-gradient(circle at 55% 40%,#8a7a6a,#2a2e38 50%,#12151c)"></div>

  <div class="band band--alt" style="top:787px;height:245px"></div>
  <h2 class="sec-title" style="left:34px;top:826px">Digital Asset Education</h2>
  <div class="copy" style="left:34px;top:852px"><p>Sed ut perspiciatis unde omnis iste natus error sit voluptatem accus antium beatae enim ipsam voluptatem quia voluptas sit aspernatur aut odit aut fugit, sed quia consequuntur magni dolores eos qui ratione voluptatem sequi nesciunt.</p><p>Sed ut perspiciatis unde omnis iste natus error sit voluptatem accus antium beatae enim ipsam voluptatem quia voluptas sit aspernatur aut odit aut fugit, sed quia consequuntur magni dolores eos qui ratione voluptatem sequi nesciunt.</p></div>
  <div class="btn" style="left:35px;top:966px">Sign Up Now</div>
  <div class="media tilt" role="img" aria-label="Laptop showing digital asset screen on a desk" style="left:300px;top:826px;width:202px;height:170px;background:linear-gradient(135deg,#b9c2c8,#2b4a6e 50%,#1a2334)"></div>

  <h2 class="center-title" style="top:1058px">NFT Creative Art Projects</h2>
  <div class="tile" style="left:34px"><svg width="38" height="40" viewBox="0 0 38 40" fill="none" stroke="#3f5cf4" stroke-width="2"><rect x="3" y="2" width="32" height="36"/><rect x="9" y="8" width="20" height="24"/></svg>Art</div>
  <div class="tile" style="left:154px"><svg width="44" height="40" viewBox="0 0 44 40" stroke="#3f5cf4" stroke-width="2" fill="none"><path d="M4 16v8M9 12v16M14 8v24M30 8v24M35 12v16M40 16v8"/><circle cx="22" cy="20" r="8"/><path d="M20 24v-7l4-1"/></svg>Music</div>
  <div class="tile" style="left:277px"><svg width="50" height="38" viewBox="0 0 50 38" fill="none" stroke="#3f5cf4" stroke-width="2"><path d="M12 8h26c6 0 10 8 10 18 0 8-6 10-10 4l-4-5H16l-4 5c-4 6-10 4-10-4C2 16 6 8 12 8z"/><path d="M13 15v8M9 19h8"/><circle cx="34" cy="16" r="1.5"/><circle cx="38" cy="20" r="1.5"/></svg>Gaming</div>
  <div class="tile tile--more" style="left:399px"><svg width="30" height="30" viewBox="0 0 30 30"><path d="M11 0h8v11h11v8H19v11h-8V19H0v-8h11z" fill="#5f7bf7"/></svg>More</div>

  <div class="band band--deep" style="top:1230px;height:255px"></div>
  <h2 class="center-title" style="top:1261px">Videos</h2>
  <div class="thumb" role="img" aria-label="Video still of NFT marketplace on a tablet" style="left:16px;top:1325px;width:130px;height:100px;background:linear-gradient(135deg,#d8d0c4,#6e7890)"><span class="play"></span></div>
  <div class="thumb" role="img" aria-label="Video still of pixel avatar collection on a phone" style="left:152px;top:1298px;width:235px;height:152px;border:2px solid #4f6bf7;background:linear-gradient(135deg,#2e4a8a,#5b7088 50%,#3a2a2a)"><span class="play play--big"></span></div>
  <div class="thumb" role="img" aria-label="Video still of NFT gallery on a phone" style="left:395px;top:1325px;width:129px;height:100px;background:linear-gradient(135deg,#c6b89c,#4a5fb0 60%,#b05ca8)"><span class="play"></span></div>

  <div class="head-row" style="top:1506px"><h3>Podcasts</h3><a>View All</a></div>
  <div class="feature-art" role="img" aria-label="Pixel robot character on blue" style="top:1540px;background:linear-gradient(160deg,#3f5cf4,#2c46d8)"></div>
  <div class="card" style="left:195px;top:1540px"><h4>Nemo enim ipsam</h4><p>Sed ut perspiciatis unde omnis iste natus error sit voluptatem accus antium beatae.</p><div class="card-foot"><div><span>Folkbook</span><span>Chirplo</span><span>Linkpro</span></div><span>12:00 sec</span></div></div>
  <div class="card" style="left:355px;top:1540px"><h4>Nemo enim ipsam</h4><p>Sed ut perspiciatis unde omnis iste natus error sit voluptatem accus antium beatae.</p><div class="card-foot"><div><span>Folkbook</span><span>Chirplo</span><span>Linkpro</span></div><span>12:00 sec</span></div></div>
  <div class="card" style="left:195px;top:1636px"><h4>Nemo enim ipsam</h4><p>Sed ut perspiciatis unde omnis iste natus error sit voluptatem accus antium beatae.</p><div class="card-foot"><div><span>Folkbook</span><span>Chirplo</span><span>Linkpro</span></div><span>12:00 sec</span></div></div>
  <div class="card" style="left:355px;top:1636px"><h4>Nemo enim ipsam</h4><p>Sed ut perspiciatis unde omnis iste natus error sit voluptatem accus antium beatae.</p><div class="card-foot"><div><span>Folkbook</span><span>Chirplo</span><span>Linkpro</span></div><span>12:00 sec</span></div></div>

  <div class="media" role="img" aria-label="Illustration of hands reaching for floating NFT cards and coins" style="left:34px;top:1760px;width:310px;height:178px;border-radius:18px;background:linear-gradient(160deg,#2a3fb8,#1b2b86 60%,#3a57d8)"></div>
  <div class="feature"><h3>NFT Virtaul</h3><p>Sed ut perspiciatis unde omnis iste natus error sit voluptatem accus antium beatae enim ipsam voluptatem quia voluptas sit aspernatur aut odit aut fugit, sed quia consequuntur magni dolores eos qui ratione voluptatem sequi nesciunt.</p><div class="btn" style="left:12px;top:104px">Learn More</div></div>

  <div class="head-row" style="top:1966px"><h3>Crypto News</h3><a>View All</a></div>
  <div class="feature-art" role="img" aria-label="Pixel character with headphones on blue" style="top:2000px;height:182px;background:linear-gradient(160deg,#3f5cf4,#2c46d8)"></div>
  <div class="card" style="left:195px;top:2000px"><div class="date">Feb 20, 2022</div><h4>Nemo enim ipsam</h4><p>Sed ut perspiciatis unde omnis iste natus error sit voluptatem accus antium beatae.</p></div>
  <div class="card" style="left:356px;top:2000px"><div class="date">Feb 20, 2022</div><h4>Nemo enim ipsam</h4><p>Sed ut perspiciatis unde omnis iste natus error sit voluptatem accus antium beatae.</p></div>
  <div class="card" style="left:195px;top:2096px"><div class="date">Feb 20, 2022</div><h4>Nemo enim ipsam</h4><p>Sed ut perspiciatis unde omnis iste natus error sit voluptatem accus antium beatae.</p></div>
  <div class="card" style="left:356px;top:2096px"><div class="date">Feb 20, 2022</div><h4>Nemo enim ipsam</h4><p>Sed ut perspiciatis unde omnis iste natus error sit voluptatem accus antium beatae.</p></div>

  <div class="web3">
    <div class="row" style="left:34px">Web 3.0 Enabled: <span class="dot"></span><span class="vault">VeloPurse</span><span class="sq"></span><span class="vault">Tallow Vault</span></div>
    <div class="row" style="left:334px">Follow Us: <span class="social">Chirplo</span><span class="social">Wirepost</span><span class="social">Snapmora</span><span class="social">Huddlex</span></div>
  </div>
  <div class="footer">
    <div class="col" style="left:34px;width:145px"><div class="f-brand">Ledgerline Nova</div><p>Sed ut perspiciatis unde omnis iste natus error sit voluptatem accus antium beatae enim ipsam voluptatem quia voluptas sit</p></div>
    <div class="col" style="left:189px"><h5>Quick Links</h5><ul><li>Home</li><li>About Us</li><li>Services</li><li>Projects</li><li>Podcast</li><li>Latest News</li><li>ContactUs</li></ul></div>
    <div class="col" style="left:293px"><h5>Resources</h5><ul><li>Sed ut perspiciatis</li><li>Unde omnis iste</li><li>Natus error sitV</li><li>oluptatem</li><li>Accusantium</li></ul></div>
    <div class="col" style="left:398px"><h5>Subscribe</h5><p>Sed ut perspiciatis unde<br>omnis iste natus</p><div class="email">Email Address</div><div class="signup">Sign Up</div></div>
  </div>
  <div class="copyright"><span class="abs" style="left:34px;top:15px">Copyright © 2022. Company Name. All Right Reserved</span><div class="pays"><i></i><i></i><i></i><i></i><i></i><i></i><i></i><i></i></div></div>
</section>

<!-- ============ LIGHT THEME ============ -->
<section class="panel panel--light">
  <div class="hero-shape"></div>
  <div class="brand">Ledgerline Nova</div>
  <nav class="nav"><span>Home</span><span>About Us</span><span>Services</span><span>Projects</span><span>Podcast</span><span>Latest News</span></nav>
  <div class="login">Log In</div>
  <svg class="cart" width="14" height="10" viewBox="0 0 14 10"><path d="M1 3h10l-1.5 5h-7z" fill="#1b1b1d"/><text x="10" y="3" font-size="4" fill="#3f5cf4" font-family="Poppins,sans-serif">(0)</text></svg>
  <h1 class="hero-title">Welcome to<br>Ledgerline Nova</h1>
  <p class="hero-sub">We are a website dedicated<br>to crypto education</p>
  <div class="btn btn--black" style="left:35px;top:189px">Read More</div>
  <div class="dots"><i></i><i></i><i></i><i></i></div>
  <div class="media" role="img" aria-label="Neon NFT artwork with pixel cat character and floating media icons" style="left:236px;top:50px;width:270px;height:205px;background:radial-gradient(circle at 50% 60%,#1e6fa0,#0d1c33 60%,#070b16);box-shadow:0 4px 10px rgba(0,0,0,.2)"></div>

  <h2 class="sec-title" style="left:34px;top:346px">Digital Asset Investing</h2>
  <div class="copy" style="left:34px;top:373px"><p>Sed ut perspiciatis unde omnis iste natus error sit voluptatem accus antium beatae enim ipsam voluptatem quia voluptas sit aspernatur aut odit aut fugit, sed quia consequuntur magni dolores eos qui ratione voluptatem sequi nesciunt.</p><p>Sed ut perspiciatis unde omnis iste natus error sit voluptatem accus antium beatae enim ipsam voluptatem quia voluptas sit aspernatur aut odit aut fugit, sed quia consequuntur magni dolores eos qui ratione voluptatem sequi nesciunt.</p></div>
  <div class="btn" style="left:35px;top:487px">Read More</div>
  <div class="media tilt" role="img" aria-label="Hand holding phone with glowing crypto interface" style="left:284px;top:344px;width:218px;height:182px;background:linear-gradient(135deg,#6aa6b4,#1c3c4a 55%,#0e1a22)"></div>

  <h2 class="sec-title" style="left:276px;top:569px">Blockchain Business<br>Solutions</h2>
  <div class="copy" style="left:277px;top:611px"><p>Sed ut perspiciatis unde omnis iste natus error sit voluptatem accus antium beatae enim ipsam voluptatem quia voluptas sit aspernatur aut odit aut fugit, sed quia consequuntur magni dolores eos qui ratione voluptatem sequi nesciunt.</p><p>Sed ut perspiciatis unde omnis iste natus error sit voluptatem accus antium beatae enim ipsam voluptatem quia voluptas sit aspernatur aut odit aut fugit, sed.</p></div>
  <div class="btn" style="left:277px;top:709px">Read More</div>
  <div class="media tilt-r" role="img" aria-label="Open hand holding a glowing network sphere" style="left:38px;top:566px;width:222px;height:186px;background:radial-gradient(circle at 55% 40%,#8a7a6a,#2a2e38 50%,#12151c)"></div>

  <div class="band band--alt" style="top:787px;height:245px"></div>
  <h2 class="sec-title" style="left:34px;top:826px">Digital Asset Education</h2>
  <div class="copy" style="left:34px;top:852px"><p>Sed ut perspiciatis unde omnis iste natus error sit voluptatem accus antium beatae enim ipsam voluptatem quia voluptas sit aspernatur aut odit aut fugit, sed quia consequuntur magni dolores eos qui ratione voluptatem sequi nesciunt.</p><p>Sed ut perspiciatis unde omnis iste natus error sit voluptatem accus antium beatae enim ipsam voluptatem quia voluptas sit aspernatur aut odit aut fugit, sed quia consequuntur magni dolores eos qui ratione voluptatem sequi nesciunt.</p></div>
  <div class="btn" style="left:35px;top:966px">Sign Up Now</div>
  <div class="media tilt" role="img" aria-label="Laptop showing digital asset screen on a desk" style="left:300px;top:826px;width:202px;height:170px;background:linear-gradient(135deg,#b9c2c8,#2b4a6e 50%,#1a2334)"></div>

  <h2 class="center-title" style="top:1058px">NFT Creative Art Projects</h2>
  <div class="tile" style="left:34px"><svg width="38" height="40" viewBox="0 0 38 40" fill="none" stroke="#3f5cf4" stroke-width="2"><rect x="3" y="2" width="32" height="36"/><rect x="9" y="8" width="20" height="24"/></svg>Art</div>
  <div class="tile" style="left:154px"><svg width="44" height="40" viewBox="0 0 44 40" stroke="#3f5cf4" stroke-width="2" fill="none"><path d="M4 16v8M9 12v16M14 8v24M30 8v24M35 12v16M40 16v8"/><circle cx="22" cy="20" r="8"/><path d="M20 24v-7l4-1"/></svg>Music</div>
  <div class="tile" style="left:277px"><svg width="50" height="38" viewBox="0 0 50 38" fill="none" stroke="#3f5cf4" stroke-width="2"><path d="M12 8h26c6 0 10 8 10 18 0 8-6 10-10 4l-4-5H16l-4 5c-4 6-10 4-10-4C2 16 6 8 12 8z"/><path d="M13 15v8M9 19h8"/><circle cx="34" cy="16" r="1.5"/><circle cx="38" cy="20" r="1.5"/></svg>Gaming</div>
  <div class="tile tile--more" style="left:399px"><svg width="30" height="30" viewBox="0 0 30 30"><path d="M11 0h8v11h11v8H19v11h-8V19H0v-8h11z" fill="#5f7bf7"/></svg>More</div>

  <div class="band band--deep" style="top:1230px;height:255px"></div>
  <h2 class="center-title" style="top:1261px">Videos</h2>
  <div class="thumb" role="img" aria-label="Video still of NFT marketplace on a tablet" style="left:16px;top:1325px;width:130px;height:100px;background:linear-gradient(135deg,#d8d0c4,#6e7890)"><span class="play"></span></div>
  <div class="thumb" role="img" aria-label="Video still of pixel avatar collection on a phone" style="left:152px;top:1298px;width:235px;height:152px;border:2px solid #1b1b1d;background:linear-gradient(135deg,#2e4a8a,#5b7088 50%,#3a2a2a)"><span class="play play--big"></span></div>
  <div class="thumb" role="img" aria-label="Video still of NFT gallery on a phone" style="left:395px;top:1325px;width:129px;height:100px;background:linear-gradient(135deg,#c6b89c,#4a5fb0 60%,#b05ca8)"><span class="play"></span></div>

  <div class="head-row" style="top:1506px"><h3>Podcasts</h3><a>View All</a></div>
  <div class="feature-art" role="img" aria-label="Pixel robot character on blue" style="top:1540px;background:linear-gradient(160deg,#3f5cf4,#2c46d8)"></div>
  <div class="card" style="left:195px;top:1540px"><h4>Nemo enim ipsam</h4><p>Sed ut perspiciatis unde omnis iste natus error sit voluptatem accus antium beatae.</p><div class="card-foot"><div><span>Folkbook</span><span>Chirplo</span><span>Linkpro</span></div><span>12:00 sec</span></div></div>
  <div class="card" style="left:355px;top:1540px"><h4>Nemo enim ipsam</h4><p>Sed ut perspiciatis unde omnis iste natus error sit voluptatem accus antium beatae.</p><div class="card-foot"><div><span>Folkbook</span><span>Chirplo</span><span>Linkpro</span></div><span>12:00 sec</span></div></div>
  <div class="card" style="left:195px;top:1636px"><h4>Nemo enim ipsam</h4><p>Sed ut perspiciatis unde omnis iste natus error sit voluptatem accus antium beatae.</p><div class="card-foot"><div><span>Folkbook</span><span>Chirplo</span><span>Linkpro</span></div><span>12:00 sec</span></div></div>
  <div class="card" style="left:355px;top:1636px"><h4>Nemo enim ipsam</h4><p>Sed ut perspiciatis unde omnis iste natus error sit voluptatem accus antium beatae.</p><div class="card-foot"><div><span>Folkbook</span><span>Chirplo</span><span>Linkpro</span></div><span>12:00 sec</span></div></div>

  <div class="media" role="img" aria-label="Illustration of hands reaching for floating NFT cards and coins" style="left:34px;top:1760px;width:310px;height:178px;border-radius:18px;background:linear-gradient(160deg,#2a3fb8,#1b2b86 60%,#3a57d8)"></div>
  <div class="feature"><h3>NFT Virtaul</h3><p>Sed ut perspiciatis unde omnis iste natus error sit voluptatem accus antium beatae enim ipsam voluptatem quia voluptas sit aspernatur aut odit aut fugit, sed quia consequuntur magni dolores eos qui ratione voluptatem sequi nesciunt.</p><div class="btn" style="left:12px;top:104px">Learn More</div></div>

  <div class="head-row" style="top:1966px"><h3>Crypto News</h3><a>View All</a></div>
  <div class="feature-art" role="img" aria-label="Pixel character with headphones on blue" style="top:2000px;height:182px;background:linear-gradient(160deg,#3f5cf4,#2c46d8)"></div>
  <div class="card" style="left:195px;top:2000px"><div class="date">Feb 20, 2022</div><h4>Nemo enim ipsam</h4><p>Sed ut perspiciatis unde omnis iste natus error sit voluptatem accus antium beatae.</p></div>
  <div class="card" style="left:356px;top:2000px"><div class="date">Feb 20, 2022</div><h4>Nemo enim ipsam</h4><p>Sed ut perspiciatis unde omnis iste natus error sit voluptatem accus antium beatae.</p></div>
  <div class="card" style="left:195px;top:2096px"><div class="date">Feb 20, 2022</div><h4>Nemo enim ipsam</h4><p>Sed ut perspiciatis unde omnis iste natus error sit voluptatem accus antium beatae.</p></div>
  <div class="card" style="left:356px;top:2096px"><div class="date">Feb 20, 2022</div><h4>Nemo enim ipsam</h4><p>Sed ut perspiciatis unde omnis iste natus error sit voluptatem accus antium beatae.</p></div>

  <div class="web3">
    <div class="row" style="left:34px">Web 3.0 Enabled: <span class="dot"></span><span class="vault">VeloPurse</span><span class="sq"></span><span class="vault">Tallow Vault</span></div>
    <div class="row" style="left:334px">Follow Us: <span class="social">Chirplo</span><span class="social">Wirepost</span><span class="social">Snapmora</span><span class="social">Huddlex</span></div>
  </div>
  <div class="footer">
    <div class="col" style="left:34px;width:145px"><div class="f-brand">Ledgerline Nova</div><p>Sed ut perspiciatis unde omnis iste natus error sit voluptatem accus antium beatae enim ipsam voluptatem quia voluptas sit</p></div>
    <div class="col" style="left:189px"><h5>Quick Links</h5><ul><li>Home</li><li>About Us</li><li>Services</li><li>Projects</li><li>Podcast</li><li>Latest News</li><li>ContactUs</li></ul></div>
    <div class="col" style="left:293px"><h5>Resources</h5><ul><li>Sed ut perspiciatis</li><li>Unde omnis iste</li><li>Natus error sitV</li><li>oluptatem</li><li>Accusantium</li></ul></div>
    <div class="col" style="left:398px"><h5>Subscribe</h5><p>Sed ut perspiciatis unde<br>omnis iste natus</p><div class="email">Email Address</div><div class="signup">Sign Up</div></div>
  </div>
  <div class="copyright"><span class="abs" style="left:34px;top:15px">Copyright © 2022. Company Name. All Right Reserved</span><div class="pays"><i></i><i></i><i></i><i></i><i></i><i></i><i></i><i></i></div></div>
</section>

</div>
</body>
</html>
```